Corvane Holdings , new business card design

investment firm with corporate clients . need double sided business card , vertical and horizontal options ,logo must be clear. prefer pantone colors only and sharp design. website also www.corvane.ae

Khalid Bin Tarrafi
Managing Director
Tel. +971 4 387 2940
Mobile +971 50 518 2403
khalid@corvane.ae
Q-Span Plaza, officw 18-B07, Warqa Gardens, Dubai

Contact Information for Business Card

Khalid Bin Tarrafi
Managing Director

Font styles to use
Serif

Colors

Designer to choose colors to be used in the design.

```html
<!DOCTYPE html>
<html lang="en">
<head>
<meta charset="utf-8">
<title>Corvane Holdings – Business Card</title>
<link href="https://fonts.googleapis.com/css2?family=Roboto:wght@400;500&family=Roboto+Condensed:wght@500&family=Open+Sans:wght@600&display=swap" rel="stylesheet">
<style>
  :root {
    --backdrop: #e4e4e2;
    --card-white: #f7f7f7;
    --brand-blue: #4a7399;
    --name-blue: #4b76a0;
    --ink: #1f1f1f;
    --text-grey: #4a4a4a;
    --rule-grey: #6b6b6b;
    --white: #ffffff;
  }
  * { margin: 0; padding: 0; box-sizing: border-box; }
  html, body {
    width: 1200px; height: 960px; overflow: hidden;
    background: var(--backdrop);
    font-family: "Roboto", Arial, sans-serif;
  }
  .canvas { position: relative; width: 1200px; height: 960px; }

  .card {
    position: absolute;
    width: 600px; height: 342px;
    box-shadow: 0 2px 6px rgba(0,0,0,0.18);
  }
  .card--front { left: 322px; top: 108px; background: var(--card-white); }
  .card--back  { left: 320px; top: 493px; background: var(--brand-blue); }

  .brand {
    position: absolute;
    display: flex; align-items: center; gap: 12px;
    font-family: "Roboto", Arial, sans-serif;
    font-weight: 400;
    text-transform: uppercase;
    white-space: nowrap;
  }
  .brand__mark { display: block; }
  .card--front .brand {
    right: 40px; top: 62px;
    font-size: 22px; letter-spacing: 5px;
    color: var(--ink);
  }
  .card--front .brand__mark { width: 14px; height: 14px; background: var(--brand-blue); }
  .card--back .brand {
    left: 0; right: 0; top: 152px; justify-content: center;
    font-size: 30px; letter-spacing: 7px;
    color: var(--white);
  }
  .card--back .brand__mark { width: 18px; height: 18px; background: var(--white); }

  .holder { position: absolute; left: 37px; top: 162px; }
  .holder__name {
    font-family: "Roboto Condensed", "Arial Narrow", sans-serif;
    font-weight: 500; font-size: 21px;
    color: var(--name-blue); line-height: 26px;
  }
  .holder__title {
    font-family: "Open Sans", Arial, sans-serif;
    font-weight: 600; font-size: 14px;
    color: var(--ink); line-height: 20px;
  }

  .contacts { position: absolute; left: 38px; top: 224px; list-style: none; }
  .contacts li {
    display: flex; align-items: center; gap: 6px;
    height: 19px; font-size: 14px; color: var(--text-grey);
  }
  .contacts svg { width: 12px; height: 12px; fill: var(--brand-blue); flex: none; }

  .address {
    position: absolute; right: 38px; top: 240px;
    text-align: right; font-size: 14px; line-height: 19px;
    color: var(--text-grey); font-style: normal;
  }

  .rule {
    position: absolute; left: 0; right: 0; top: 305px;
    height: 1px; background: var(--rule-grey);
  }
  .web {
    position: absolute; left: 328px; top: 294px;
    width: 235px; height: 26px;
    background: var(--brand-blue); color: var(--white);
    font-size: 14px; letter-spacing: 4px;
    display: flex; align-items: center; justify-content: center;
  }
</style>
</head>
<body>
<main class="canvas">
  <section class="card card--front" aria-label="Business card front">
    <div class="brand"><span class="brand__mark"></span>Corvane Holdings</div>

    <div class="holder">
      <p class="holder__name">Khalid Bin Tarrafi</p>
      <p class="holder__title">Managing Director</p>
    </div>

    <ul class="contacts">
      <li>
        <svg viewBox="0 0 12 12" aria-hidden="true"><path d="M2.4 0.6 L4.2 2.8 L3.2 4.2 C3.9 5.7 6.3 8.1 7.8 8.8 L9.2 7.8 L11.4 9.6 L10.2 11.4 C5.6 11.2 0.8 6.4 0.6 1.8 Z"/></svg>
        +971 4 387 2940
      </li>
      <li>
        <svg viewBox="0 0 12 12" aria-hidden="true"><path d="M3 0 H9 A1 1 0 0 1 10 1 V11 A1 1 0 0 1 9 12 H3 A1 1 0 0 1 2 11 V1 A1 1 0 0 1 3 0 Z M3.2 1.4 V9.4 H8.8 V1.4 Z M5.4 10.2 H6.6 V11 H5.4 Z"/></svg>
        +971 50 518 2403
      </li>
      <li>
        <svg viewBox="0 0 12 12" aria-hidden="true"><path d="M0.5 2.5 H11.5 V10 H0.5 Z M1.4 3.3 L6 6.8 L10.6 3.3 V3.2 H1.4 Z" fill-rule="evenodd"/></svg>
        khalid@corvane.ae
      </li>
    </ul>

    <address class="address">Q-Span Plaza, officw 18-B07<br>Warqa Gardens, Dubai</address>

    <div class="rule"></div>
    <div class="web">www.corvane.ae</div>
  </section>

  <section class="card card--back" aria-label="Business card back">
    <div class="brand"><span class="brand__mark"></span>Corvane Holdings</div>
  </section>
</main>
</body>
</html>
```